Meridale Bed Company Needs Business Card

Looking for a very nice looking business card. Creative but not extravagant. We sell beds and pillows across the U.S. and need something professional but catchy. I have attached the logo.

Name : Devin Holt
Title : President
Phone : (800) 471-2960
Email: sleep@quilmora.com
Website: www.quilmora.com

Can be single-sided or double-sided
horizontal or vertical

Can use Blues/Greys

Target Market(s)

Mass Market

Industry/Entity Type

Retail

Contact Information for Business Card

Name : Devin Holt
Title : President
Phone : (800) 471-2960
Email: sleep@quilmora.com
Website: www.quilmora.com

Requirements
Must have
• Clean, Modern, Smooth
• Can use Blues/Greys
• On the other side without the information - have something simple like www.quilmora.com or our logo
Nice to have
• Surprise me
Should not have
• Nothing crazy, nothing cluttered

```html
<!DOCTYPE html>
<html lang="en">
<head>
<meta charset="utf-8">
<title>Quilmora Business Card</title>
<link rel="stylesheet" href="https://fonts.googleapis.com/css2?family=Open+Sans:wght@300;400;600&display=swap">
<style>
  :root {
    --stage-top: #2b2b2b;
    --stage-bottom: #050505;
    --card-white: #ffffff;
    --brand-blue: #2a9bd7;
    --back-blue: #3aade2;
    --ink: #2e2e2e;
    --on-blue: #ffffff;
  }
  * { margin: 0; padding: 0; box-sizing: border-box; }
  html, body {
    width: 1200px;
    height: 900px;
    overflow: hidden;
  }
  body {
    position: relative;
    background: linear-gradient(180deg, var(--stage-top) 0%, #1a1a1a 45%, var(--stage-bottom) 100%);
    font-family: "Open Sans", Arial, sans-serif;
  }
  .card {
    position: absolute;
    top: 306px;
    width: 440px;
    height: 271px;
    border-radius: 12px;
    text-align: center;
  }
  .card-front {
    left: 149px;
    background: var(--card-white);
  }
  .card-back {
    left: 608px;
    background: var(--back-blue);
    display: flex;
    align-items: center;
    justify-content: center;
  }
  .brand-name {
    font-weight: 300;
    line-height: 1;
    letter-spacing: 1px;
  }
  .card-front .brand-name {
    margin-top: 30px;
    font-size: 66px;
    color: var(--brand-blue);
  }
  .card-back .brand-name {
    font-size: 68px;
    color: var(--on-blue);
  }
  .person-name {
    margin-top: 22px;
    font-size: 18px;
    font-weight: 600;
    color: var(--brand-blue);
    line-height: 1.2;
  }
  .person-title {
    font-size: 13px;
    color: var(--ink);
    line-height: 1.4;
  }
  .contact-icons {
    margin-top: 18px;
    display: flex;
    justify-content: center;
    gap: 5px;
    height: 10px;
  }
  .contact-icons svg { width: 9px; height: 9px; fill: var(--brand-blue); }
  .contact-list {
    margin-top: 3px;
    list-style: none;
    font-size: 13px;
    color: var(--ink);
    line-height: 16px;
  }
</style>
</head>
<body>
  <section class="card card-front" aria-label="Business card front">
    <div class="brand-name">quilmora</div>
    <div class="person-name">Devin Holt</div>
    <div class="person-title">President</div>
    <div class="contact-icons" aria-hidden="true">
      <svg viewBox="0 0 10 10"><path d="M1 3 Q5 0 9 3 L8 4.5 L6.5 3.8 L6.5 3 Q5 2.5 3.5 3 L3.5 3.8 L2 4.5 Z M2.5 5 H7.5 L8.5 9 H1.5 Z"/></svg>
      <svg viewBox="0 0 10 10"><path d="M1 2.5 H9 V8 H1 Z" /><path d="M1 2.5 L5 5.5 L9 2.5" stroke="#fff" stroke-width="0.8" fill="none"/></svg>
      <svg viewBox="0 0 10 10"><circle cx="5" cy="5" r="4.2"/><path d="M3 3 Q4.5 4 3.5 6 M6 2 Q7.5 4 6.5 7" stroke="#fff" stroke-width="0.8" fill="none"/></svg>
    </div>
    <ul class="contact-list">
      <li>(800) 471-2960</li>
      <li>sleep@quilmora.com</li>
      <li>www.quilmora.com</li>
    </ul>
  </section>

  <section class="card card-back" aria-label="Business card back">
    <div class="brand-name">quilmora</div>
  </section>
</body>
</html>
```